Redesign 2016 Digital Marketing Website and Convert to Wordpress

Technology needed to integrate:

- redesign and convert to wordpress
- gravity forms
- malware and hacker defense / honeypot (must be very secure from hackers)
- I want gravity forms to be a flow that asks many questions with icons and progress bar.
- 1 home page design
- 1 blog design
- 1 design for internal page content
- 1 multi step gravity form
I want to focus on SMB's. We are a marketing agency thats been around since 2016.

Site is: tallpine.agency

I am looking to redesign the homepage, blog page and services page. The services page will be a template for all inner pages of the site. All content needs to be moved into the new design.

I want to get ride of the weird video.

I need you to install gravity forms pro model so we can pass utms.

I need the gravity form to be a multi step form with icons.

All "contact us" or "get a free assesments" call to actions will go to this form only.

step 1:
what is your website

step 2:
what industry are you in
- option
- Home Services
- Legal
- Ecommerce
- Lead Gen

No matter which one they select its going to produce a differnt calculator for them.

Law:
How many leads did you get last month
how much is each ase worth on average
How much revenue do you want to make

Home servicse:
How many bookings did you get last month
How much is each service worht on average
How much revenue do you wangt to make

Ecommerce:
What is your average order value
How muny purchases did you have last month
How much revenue did you drive
How much revenue do you want to drive

For lead gen:
How many leads did you get lawt month
How much revenue did they generate

Step 3:
What is your current advertising budget

step 4:
Do you have a CRM and if so what is it

Step 5:
What is your personal informagtion
name
email
phone

Let me know if this is enough to get you going

Small and medium sized law firms, ecommerce, home services and lead gen customers.

We are a digital marketing agency

• Use whats on the current site and improve upon it

• Must be very secure, developed into a wordpress website. using gravity forms. remove my photo and my staffs photo, depersonalize it so it doesnt mention me or sam crolley. Use the same color scheme. I am looking to redesign the homepage, blog page and services page. The services page will be a template for all inner pages of the site. All content needs to be moved into the new design. I want to get ride of the weird video. I need you to install gravity forms pro model so we can pass utms. I need the gravity form to be a multi step form with icons. All "contact us" or "get a free assesments" call to actions will go to this form only. step 1: what is your website step 2: what industry are you in - option - Home Services - Legal - Ecommerce - Lead Gen No matter which one they select its going to produce a differnt calculator for them. Law: How many leads did you get last month how much is each ase worth on average How much revenue do you want to make Home servicse: How many bookings did you get last month How much is each service worht on average How much revenue do you wangt to make Ecommerce: What is your average order value How muny purchases did you have last month How much revenue did you drive How much revenue do you want to drive For lead gen: How many leads did you get lawt month How much revenue did they generate How much revenue do you want to make Step 3: What is your current advertising budget step 4: Do you have a CRM and if so what is it Step 5: What is your personal informagtion name email phone Let me know if this is enough to get you going
• SHOULD NOT BE SLOPPY, I AM LOOKING FOR ATTENTION TO DETAIL.

```html
<!DOCTYPE html>
<html lang="en">
<head>
<meta charset="utf-8">
<title>Tall Pine – Free Assessment Flow</title>
<link rel="stylesheet" href="https://fonts.googleapis.com/css2?family=Poppins:wght@400;500;600;700;800&display=swap">
<style>
:root{
  --board:#6e1216;
  --brand:#7b1417;
  --accent:#f7941d;
  --nav:#2c2c2c;
  --ink:#222;
  --muted:#555;
  --soft:#9a9a9a;
  --rule:#e6e6e6;
  --field:#cfcfcf;
  --badge:#e9e9e9;
  --navy:#1f3c63;
}
*{box-sizing:border-box;margin:0;padding:0}
html,body{width:1200px;height:870px;overflow:hidden}
body{background:var(--board);font-family:"Poppins",sans-serif;color:var(--ink);position:relative}

.page{position:absolute;width:376px;height:404px;background:#fff;overflow:hidden}
.page--one{left:16px;top:33px}
.page--two{left:411px;top:33px}
.page--three{left:805px;top:33px}
.page--four{left:204px;top:452px}
.page--five{left:599px;top:452px}

/* header */
.site-header{position:absolute;left:0;top:0;width:100%;height:28px}
.brand{position:absolute;left:24px;top:5px;display:flex;align-items:center;gap:5px}
.brand__mark{width:19px;height:19px;border-radius:50%;background:var(--brand)}
.brand__name{font-size:7.8px;letter-spacing:.6px;color:var(--muted);line-height:1}
.brand__tag{display:block;font-size:2.6px;letter-spacing:1.3px;margin-top:2px;color:var(--muted)}
.call{position:absolute;left:177px;top:10.5px;font-size:5.6px;font-weight:600;color:var(--ink)}
.call b{color:var(--brand);font-weight:700}
.btn-cta{position:absolute;left:283px;top:6.5px;width:70px;height:15px;background:var(--accent);color:#fff;font-size:4.8px;font-weight:600;display:flex;align-items:center;justify-content:center;letter-spacing:.2px}
.main-nav{position:absolute;left:0;top:28px;width:100%;height:17.5px;background:var(--nav);display:flex;justify-content:center;align-items:center;gap:14px;font-size:4.2px;color:#fff;letter-spacing:.2px}

/* form area */
.form-title{position:absolute;left:0;top:62px;width:100%;text-align:center;font-size:11.4px;font-weight:700;letter-spacing:.2px}
.form-title::after{content:"";display:block;width:32px;height:1.5px;background:var(--brand);margin:4px auto 0}
.tracker{position:absolute;left:85px;top:95px;display:flex;align-items:center}
.tracker__dot{width:18px;height:18px;border-radius:50%;border:1.2px solid #d2d2d2;color:#b5b5b5;font-size:7px;font-weight:600;display:flex;align-items:center;justify-content:center}
.tracker__dot.is-done{border-color:var(--brand);color:var(--brand)}
.tracker__line{width:29px;height:1px;background:#d2d2d2}
.tracker__line.is-done{background:var(--brand)}
.tracker__line.is-half{background:linear-gradient(90deg,var(--brand) 50%,#d2d2d2 50%)}

.step-head{position:absolute;left:91px;top:130px;display:flex;gap:4px;align-items:center}
.step-head svg{width:14px;height:14px}
.step-head__num{font-size:5.8px;font-weight:700;color:var(--brand);line-height:1.3}
.step-head__q{font-size:5.2px;font-weight:500;line-height:1.4}
.field{position:absolute;height:16px;border:.6px solid var(--field);font-size:3.8px;color:#444;display:flex;align-items:center;padding-left:6px;justify-content:space-between;padding-right:5px}
.field--main{left:91.5px;top:150px;width:155px}
.btn-next{position:absolute;left:249px;top:150px;width:36px;height:16px;background:var(--nav);color:#fff;font-size:6px;font-weight:700;display:flex;align-items:center;justify-content:center;gap:3px}
.field--name{left:91px;top:150px;width:75px}
.field--phone{left:171px;top:150px;width:75px}
.field--email{left:91px;top:169px;width:155px}
.btn-submit{position:absolute;left:249px;top:150px;width:40px;height:35px;background:var(--accent);color:#fff;font-size:6px;font-weight:700;display:flex;align-items:center;justify-content:center;gap:3px}

/* footer */
.trust{position:absolute;left:0;top:207px;width:100%;height:47px;border-top:.6px solid var(--rule);border-bottom:.6px solid var(--rule)}
.trust .brand{top:14px}
.trust__badge{position:absolute;left:130px;top:10px;width:65px;height:27px;background:var(--badge);border-left:7px solid #e03a2f}
.trust__seal{position:absolute;left:215px;top:10px;width:27px;height:27px;border-radius:50%;background:var(--navy)}
.follow{position:absolute;left:277px;top:11px;font-size:5.8px;font-weight:500}
.follow__row{display:flex;gap:10px;margin-top:6px}
.follow__row span{width:8px;height:8px;border-radius:50%;background:#333}

.links{position:absolute;left:0;top:268px;width:100%}
.links__col{position:absolute;top:0}
.links__col h4{font-size:7px;font-weight:700;letter-spacing:.2px;margin-bottom:4px;color:#333}
.links__col li{list-style:none;font-size:4px;color:var(--muted);height:10.3px}
.links__col--guides li{height:17px;width:72px;line-height:1.55}
.col-quick{left:24px}
.col-services{left:100px}
.col-industries{left:193px}
.col-guides{left:277px}
.legal{position:absolute;left:0;top:378px;width:100%;height:26px;border-top:.6px solid var(--rule);text-align:center;font-size:4px;color:var(--muted);padding-top:10px}
</style>
</head>
<body>

<!-- Step 1 -->
<section class="page page--one">
  <header class="site-header">
    <div class="brand"><span class="brand__mark"></span><span class="brand__name">TALL PINE<span class="brand__tag">GROWTH MARKETING</span></span></div>
    <p class="call">OR CALL US NOW : <b>(480) 555-0142</b></p>
    <a class="btn-cta">GROW YOUR REVENUE</a>
  </header>
  <nav class="main-nav"><span>HOME</span><span>ABOUT</span><span>INDUSTRIES</span><span>SERVICES</span><span>BLOG</span><span>CONTACT US</span></nav>
  <h1 class="form-title">GET A FREE ASSESSMENTS</h1>
  <div class="tracker">
    <span class="tracker__dot is-done">1</span><span class="tracker__line is-half"></span>
    <span class="tracker__dot">2</span><span class="tracker__line"></span>
    <span class="tracker__dot">3</span><span class="tracker__line"></span>
    <span class="tracker__dot">4</span><span class="tracker__line"></span>
    <span class="tracker__dot">5</span>
  </div>
  <div class="step-head">
    <svg viewBox="0 0 14 14" fill="none" stroke="#7b1417" stroke-width=".6"><circle cx="7" cy="7" r="6"/><ellipse cx="7" cy="7" rx="2.6" ry="6"/><path d="M1 7h12M2 4h10M2 10h10"/><rect x="1.5" y="5.3" width="11" height="3.4" fill="#fff"/></svg>
    <div><p class="step-head__num">Step 1</p><p class="step-head__q">What is your website</p></div>
  </div>
  <div class="field field--main">Enter business name</div>
  <a class="btn-next">NEXT <svg width="4" height="6" viewBox="0 0 4 6"><path d="M1 .5 3 3 1 5.5" fill="none" stroke="#fff" stroke-width=".7"/></svg></a>
  <div class="trust">
    <div class="brand"><span class="brand__mark"></span><span class="brand__name">TALL PINE<span class="brand__tag">GROWTH MARKETING</span></span></div>
    <span class="trust__badge"></span><span class="trust__seal"></span>
    <div class="follow">FOLLOW US<div class="follow__row"><span></span><span></span><span></span><span></span><span></span></div></div>
  </div>
  <div class="links">
    <ul class="links__col col-quick"><h4>QUICK LINKS</h4><li>About</li><li>Industries</li><li>Services</li><li>Resources</li><li>Training</li><li>Blog</li><li>Contact Us</li></ul>
    <ul class="links__col col-services"><h4>SERVICES</h4><li>Programmatic Advertising</li><li>Search Engine Marketing (SEM)</li><li>Search Engine Optimization (SEO)</li><li>Content Marketing</li><li>Email Marketing</li><li>Paid Search Advertising</li><li>Paid Social Advertising</li></ul>
    <ul class="links__col col-industries"><h4>INDUSTRIES</h4><li>Ecommerce</li><li>Electricians</li><li>Financial Services Marketing</li><li>Home Builders</li><li>Home Services</li><li>Hvac Companies</li><li>Cosmetic Surgery Centers</li><li>Dental Marketing</li></ul>
    <ul class="links__col links__col--guides col-guides"><h4>GUIDES</h4><li>Ultimate Guide On Growing Your Medical Practice Business</li><li>Legal Marketing Strategy Guide For Law Firm Offices</li><li>Ultimate Story Ads Guide To Skyrocket Your Leads And Sales</li><li>Ultimate Guide To Search Engine Queries</li></ul>
  </div>
  <footer class="legal">Copyright © 2024 CompanyName &nbsp;All Rights Reserved. Privacy Policy, Terms Of Use, Press &amp; Media, Cookie Policy</footer>
</section>

<!-- Step 2 -->
<section class="page page--two">
  <header class="site-header">
    <div class="brand"><span class="brand__mark"></span><span class="brand__name">TALL PINE<span class="brand__tag">GROWTH MARKETING</span></span></div>
    <p class="call">OR CALL US NOW : <b>(480) 555-0142</b></p>
    <a class="btn-cta">GROW YOUR REVENUE</a>
  </header>
  <nav class="main-nav"><span>HOME</span><span>ABOUT</span><span>INDUSTRIES</span><span>SERVICES</span><span>BLOG</span><span>CONTACT US</span></nav>
  <h1 class="form-title">GET A FREE ASSESSMENTS</h1>
  <div class="tracker">
    <span class="tracker__dot is-done">1</span><span class="tracker__line is-done"></span>
    <span class="tracker__dot is-done">2</span><span class="tracker__line is-half"></span>
    <span class="tracker__dot">3</span><span class="tracker__line"></span>
    <span class="tracker__dot">4</span><span class="tracker__line"></span>
    <span class="tracker__dot">5</span>
  </div>
  <div class="step-head">
    <svg viewBox="0 0 14 14" fill="none" stroke="#7b1417" stroke-width=".6"><rect x="2" y="1" width="6" height="12"/><rect x="8" y="5" width="4.5" height="8"/><path d="M3.3 3h1.2M5.6 3h1.2M3.3 5h1.2M5.6 5h1.2M3.3 7h1.2M5.6 7h1.2M3.3 9h1.2M5.6 9h1.2M9.3 7h2M9.3 9h2M9.3 11h2M1 13h12"/></svg>
    <div><p class="step-head__num">Step 2</p><p class="step-head__q">What industry are you in</p></div>
  </div>
  <div class="field field--main">Select Option <svg width="3" height="5" viewBox="0 0 3 5"><path d="M.3 2 1.5.6 2.7 2M.3 3 1.5 4.4 2.7 3" fill="none" stroke="#333" stroke-width=".5"/></svg></div>
  <a class="btn-next">NEXT <svg width="4" height="6" viewBox="0 0 4 6"><path d="M1 .5 3 3 1 5.5" fill="none" stroke="#fff" stroke-width=".7"/></svg></a>
  <div class="trust">
    <div class="brand"><span class="brand__mark"></span><span class="brand__name">TALL PINE<span class="brand__tag">GROWTH MARKETING</span></span></div>
    <span class="trust__badge"></span><span class="trust__seal"></span>
    <div class="follow">FOLLOW US<div class="follow__row"><span></span><span></span><span></span><span></span><span></span></div></div>
  </div>
  <div class="links">
    <ul class="links__col col-quick"><h4>QUICK LINKS</h4><li>About</li><li>Industries</li><li>Services</li><li>Resources</li><li>Training</li><li>Blog</li><li>Contact Us</li></ul>
    <ul class="links__col col-services"><h4>SERVICES</h4><li>Programmatic Advertising</li><li>Search Engine Marketing (SEM)</li><li>Search Engine Optimization (SEO)</li><li>Content Marketing</li><li>Email Marketing</li><li>Paid Search Advertising</li><li>Paid Social Advertising</li></ul>
    <ul class="links__col col-industries"><h4>INDUSTRIES</h4><li>Ecommerce</li><li>Electricians</li><li>Financial Services Marketing</li><li>Home Builders</li><li>Home Services</li><li>Hvac Companies</li><li>Cosmetic Surgery Centers</li><li>Dental Marketing</li></ul>
    <ul class="links__col links__col--guides col-guides"><h4>GUIDES</h4><li>Ultimate Guide On Growing Your Medical Practice Business</li><li>Legal Marketing Strategy Guide For Law Firm Offices</li><li>Ultimate Story Ads Guide To Skyrocket Your Leads And Sales</li><li>Ultimate Guide To Search Engine Queries</li></ul>
  </div>
  <footer class="legal">Copyright © 2024 CompanyName &nbsp;All Rights Reserved. Privacy Policy, Terms Of Use, Press &amp; Media, Cookie Policy</footer>
</section>

<!-- Step 3 -->
<section class="page page--three">
  <header class="site-header">
    <div class="brand"><span class="brand__mark"></span><span class="brand__name">TALL PINE<span class="brand__tag">GROWTH MARKETING</span></span></div>
    <p class="call">OR CALL US NOW : <b>(480) 555-0142</b></p>
    <a class="btn-cta">GROW YOUR REVENUE</a>
  </header>
  <nav class="main-nav"><span>HOME</span><span>ABOUT</span><span>INDUSTRIES</span><span>SERVICES</span><span>BLOG</span><span>CONTACT US</span></nav>
  <h1 class="form-title">GET A FREE ASSESSMENTS</h1>
  <div class="tracker">
    <span class="tracker__dot is-done">1</span><span class="tracker__line is-done"></span>
    <span class="tracker__dot is-done">2</span><span class="tracker__line is-done"></span>
    <span class="tracker__dot is-done">3</span><span class="tracker__line is-half"></span>
    <span class="tracker__dot">4</span><span class="tracker__line"></span>
    <span class="tracker__dot">5</span>
  </div>
  <div class="step-head">
    <svg viewBox="0 0 14 14" fill="none" stroke="#7b1417" stroke-width=".6"><rect x="3" y="1" width="8" height="12" rx=".6"/><rect x="4.3" y="2.4" width="5.4" height="2.4"/><path d="M4.6 6.5h1M6.5 6.5h1M8.4 6.5h1M4.6 8.5h1M6.5 8.5h1M8.4 8.5h1M4.6 10.7h1M6.5 10.7h1M8.4 10.7h1"/><circle cx="2" cy="10" r="1.6"/></svg>
    <div><p class="step-head__num">Step 3</p><p class="step-head__q">What is your current advertising budget</p></div>
  </div>
  <div class="field field--main">Enter budget</div>
  <a class="btn-next">NEXT <svg width="4" height="6" viewBox="0 0 4 6"><path d="M1 .5 3 3 1 5.5" fill="none" stroke="#fff" stroke-width=".7"/></svg></a>
  <div class="trust">
    <div class="brand"><span class="brand__mark"></span><span class="brand__name">TALL PINE<span class="brand__tag">GROWTH MARKETING</span></span></div>
    <span class="trust__badge"></span><span class="trust__seal"></span>
    <div class="follow">FOLLOW US<div class="follow__row"><span></span><span></span><span></span><span></span><span></span></div></div>
  </div>
  <div class="links">
    <ul class="links__col col-quick"><h4>QUICK LINKS</h4><li>About</li><li>Industries</li><li>Services</li><li>Resources</li><li>Training</li><li>Blog</li><li>Contact Us</li></ul>
    <ul class="links__col col-services"><h4>SERVICES</h4><li>Programmatic Advertising</li><li>Search Engine Marketing (SEM)</li><li>Search Engine Optimization (SEO)</li><li>Content Marketing</li><li>Email Marketing</li><li>Paid Search Advertising</li><li>Paid Social Advertising</li></ul>
    <ul class="links__col col-industries"><h4>INDUSTRIES</h4><li>Ecommerce</li><li>Electricians</li><li>Financial Services Marketing</li><li>Home Builders</li><li>Home Services</li><li>Hvac Companies</li><li>Cosmetic Surgery Centers</li><li>Dental Marketing</li></ul>
    <ul class="links__col links__col--guides col-guides"><h4>GUIDES</h4><li>Ultimate Guide On Growing Your Medical Practice Business</li><li>Legal Marketing Strategy Guide For Law Firm Offices</li><li>Ultimate Story Ads Guide To Skyrocket Your Leads And Sales</li><li>Ultimate Guide To Search Engine Queries</li></ul>
  </div>
  <footer class="legal">Copyright © 2024 CompanyName &nbsp;All Rights Reserved. Privacy Policy, Terms Of Use, Press &amp; Media, Cookie Policy</footer>
</section>

<!-- Step 4 -->
<section class="page page--four">
  <header class="site-header">
    <div class="brand"><span class="brand__mark"></span><span class="brand__name">TALL PINE<span class="brand__tag">GROWTH MARKETING</span></span></div>
    <p class="call">OR CALL US NOW : <b>(480) 555-0142</b></p>
    <a class="btn-cta">GROW YOUR REVENUE</a>
  </header>
  <nav class="main-nav"><span>HOME</span><span>ABOUT</span><span>INDUSTRIES</span><span>SERVICES</span><span>BLOG</span><span>CONTACT US</span></nav>
  <h1 class="form-title">GET A FREE ASSESSMENTS</h1>
  <div class="tracker">
    <span class="tracker__dot is-done">1</span><span class="tracker__line is-done"></span>
    <span class="tracker__dot is-done">2</span><span class="tracker__line is-done"></span>
    <span class="tracker__dot is-done">3</span><span class="tracker__line is-done"></span>
    <span class="tracker__dot is-done">4</span><span class="tracker__line is-half"></span>
    <span class="tracker__dot">5</span>
  </div>
  <div class="step-head">
    <svg viewBox="0 0 14 14" fill="none" stroke="#7b1417" stroke-width=".6"><circle cx="7" cy="7.5" r="2"/><circle cx="7" cy="2" r="1.3"/><circle cx="2" cy="11.5" r="1.3"/><circle cx="12" cy="11.5" r="1.3"/><path d="M7 3.3v2.2M3.1 10.7l2.3-1.8M10.9 10.7 8.6 8.9M3.3 12.2h7.4"/></svg>
    <div><p class="step-head__num">Step 4</p><p class="step-head__q">Do you have a CRM and if so what is it</p></div>
  </div>
  <div class="field field--main">Enter CRM details</div>
  <a class="btn-next">NEXT <svg width="4" height="6" viewBox="0 0 4 6"><path d="M1 .5 3 3 1 5.5" fill="none" stroke="#fff" stroke-width=".7"/></svg></a>
  <div class="trust">
    <div class="brand"><span class="brand__mark"></span><span class="brand__name">TALL PINE<span class="brand__tag">GROWTH MARKETING</span></span></div>
    <span class="trust__badge"></span><span class="trust__seal"></span>
    <div class="follow">FOLLOW US<div class="follow__row"><span></span><span></span><span></span><span></span><span></span></div></div>
  </div>
  <div class="links">
    <ul class="links__col col-quick"><h4>QUICK LINKS</h4><li>About</li><li>Industries</li><li>Services</li><li>Resources</li><li>Training</li><li>Blog</li><li>Contact Us</li></ul>
    <ul class="links__col col-services"><h4>SERVICES</h4><li>Programmatic Advertising</li><li>Search Engine Marketing (SEM)</li><li>Search Engine Optimization (SEO)</li><li>Content Marketing</li><li>Email Marketing</li><li>Paid Search Advertising</li><li>Paid Social Advertising</li></ul>
    <ul class="links__col col-industries"><h4>INDUSTRIES</h4><li>Ecommerce</li><li>Electricians</li><li>Financial Services Marketing</li><li>Home Builders</li><li>Home Services</li><li>Hvac Companies</li><li>Cosmetic Surgery Centers</li><li>Dental Marketing</li></ul>
    <ul class="links__col links__col--guides col-guides"><h4>GUIDES</h4><li>Ultimate Guide On Growing Your Medical Practice Business</li><li>Legal Marketing Strategy Guide For Law Firm Offices</li><li>Ultimate Story Ads Guide To Skyrocket Your Leads And Sales</li><li>Ultimate Guide To Search Engine Queries</li></ul>
  </div>
  <footer class="legal">Copyright © 2024 CompanyName &nbsp;All Rights Reserved. Privacy Policy, Terms Of Use, Press &amp; Media, Cookie Policy</footer>
</section>

<!-- Step 5 -->
<section class="page page--five">
  <header class="site-header">
    <div class="brand"><span class="brand__mark"></span><span class="brand__name">TALL PINE<span class="brand__tag">GROWTH MARKETING</span></span></div>
    <p class="call">OR CALL US NOW : <b>(480) 555-0142</b></p>
    <a class="btn-cta">GROW YOUR REVENUE</a>
  </header>
  <nav class="main-nav"><span>HOME</span><span>ABOUT</span><span>INDUSTRIES</span><span>SERVICES</span><span>BLOG</span><span>CONTACT US</span></nav>
  <h1 class="form-title">GET A FREE ASSESSMENTS</h1>
  <div class="tracker">
    <span class="tracker__dot is-done">1</span><span class="tracker__line is-done"></span>
    <span class="tracker__dot is-done">2</span><span class="tracker__line is-done"></span>
    <span class="tracker__dot is-done">3</span><span class="tracker__line is-done"></span>
    <span class="tracker__dot is-done">4</span><span class="tracker__line is-done"></span>
    <span class="tracker__dot is-done">5</span>
  </div>
  <div class="step-head">
    <svg viewBox="0 0 14 14" fill="none" stroke="#7b1417" stroke-width=".6"><rect x="2.5" y="1" width="9" height="12" rx=".5"/><rect x="4" y="3" width="3.5" height="4"/><path d="M8.5 3.5h1.8M8.5 5h1.8M8.5 6.5h1.8M4 9h6.3M4 10.8h6.3"/></svg>
    <div><p class="step-head__num">Step 5</p><p class="step-head__q">What is your personal information</p></div>
  </div>
  <div class="field field--name">Name</div>
  <div class="field field--phone">Phone</div>
  <div class="field field--email">Email Address</div>
  <a class="btn-submit">SUBMIT <svg width="4" height="6" viewBox="0 0 4 6"><path d="M1 .5 3 3 1 5.5" fill="none" stroke="#fff" stroke-width=".7"/></svg></a>
  <div class="trust">
    <div class="brand"><span class="brand__mark"></span><span class="brand__name">TALL PINE<span class="brand__tag">GROWTH MARKETING</span></span></div>
    <span class="trust__badge"></span><span class="trust__seal"></span>
    <div class="follow">FOLLOW US<div class="follow__row"><span></span><span></span><span></span><span></span><span></span></div></div>
  </div>
  <div class="links">
    <ul class="links__col col-quick"><h4>QUICK LINKS</h4><li>About</li><li>Industries</li><li>Services</li><li>Resources</li><li>Training</li><li>Blog</li><li>Contact Us</li></ul>
    <ul class="links__col col-services"><h4>SERVICES</h4><li>Programmatic Advertising</li><li>Search Engine Marketing (SEM)</li><li>Search Engine Optimization (SEO)</li><li>Content Marketing</li><li>Email Marketing</li><li>Paid Search Advertising</li><li>Paid Social Advertising</li></ul>
    <ul class="links__col col-industries"><h4>INDUSTRIES</h4><li>Ecommerce</li><li>Electricians</li><li>Financial Services Marketing</li><li>Home Builders</li><li>Home Services</li><li>Hvac Companies</li><li>Cosmetic Surgery Centers</li><li>Dental Marketing</li></ul>
    <ul class="links__col links__col--guides col-guides"><h4>GUIDES</h4><li>Ultimate Guide On Growing Your Medical Practice Business</li><li>Legal Marketing Strategy Guide For Law Firm Offices</li><li>Ultimate Story Ads Guide To Skyrocket Your Leads And Sales</li><li>Ultimate Guide To Search Engine Queries</li></ul>
  </div>
  <footer class="legal">Copyright © 2024 CompanyName &nbsp;All Rights Reserved. Privacy Policy, Terms Of Use, Press &amp; Media, Cookie Policy</footer>
</section>

</body>
</html>
```